Vindgerdi - Start-up company selling electricity

Hello let me tell you about Vindgerdi.

Vindgerdi is start-up company selling electricity in Iceland. The operations of the company consist of making power usage forecasts for our customers, purchasing the electricity wholesale from the energy producers, and selling the electricity to the consumer. We are focused on tech by using optimization and machine learning to minimize electricity prices to our customers. Our marketing strategy is to portray a tech company mindset and to show dedication to driving down the electricity price on the market.

We need your help to make our website pop. Possible concepts to work with are as follows:

- Iceland the land of ice and fire
- Green energy
- Innovation
- Tech and data science

Link to our website: https://prufa.vindgerdi-example.is/
We are open to ideas.
Thank you!

Target Market(s)

Electricity consumers both homes and companies.

Number of Pages Required

1 page

Font styles to use
Serif
Sans Serif

```html
<!DOCTYPE html>
<html lang="en">
<head>
<meta charset="utf-8">
<title>Vindgerdi – Electricity</title>
<link href="https://fonts.googleapis.com/css2?family=Poppins:wght@300;400;500;600&family=Cinzel:wght@700&family=EB+Garamond:wght@600&display=swap" rel="stylesheet">
<style>
:root{
  --navy:#0d3468;
  --red:#9b2d31;
  --ink:#222;
  --muted:#666;
  --white:#fff;
}
*{margin:0;padding:0;box-sizing:border-box}
html,body{width:1200px;height:2269px;overflow:hidden;background:var(--white);font-family:'Poppins',sans-serif;color:var(--ink)}
.page{position:relative;width:1200px;height:2269px}
.abs{position:absolute}
.topbar{top:0;left:0;width:1200px;height:37px;background:var(--navy);color:var(--white);font-size:11.5px;display:flex;align-items:center;padding:0 61px}
.topbar .info{margin-left:auto;display:flex;gap:38px;align-items:center}
.topbar .item{display:flex;align-items:center;gap:10px}
.ico-circle{width:26px;height:26px;border-radius:50%;background:var(--white);display:flex;align-items:center;justify-content:center}
.header{top:37px;left:0;width:1200px;height:79px;display:flex;align-items:center;padding:0 60px}
.brand{display:flex;align-items:center;gap:10px;font-family:'Poppins',sans-serif;font-weight:600;font-size:30px;color:var(--red);letter-spacing:1px}
.brand .dot{width:30px;height:30px;border-radius:50%;background:var(--navy)}
.nav{margin-left:auto;display:flex;align-items:center;gap:38px;font-size:12.5px;color:#444}
.nav .active{color:var(--red);position:relative}
.nav .active::after{content:"";position:absolute;left:50%;top:22px;width:10px;height:10px;margin-left:-5px;border-radius:50%;background:var(--navy)}
.btn{display:inline-flex;align-items:center;justify-content:space-between;border-radius:22px;color:var(--white);font-size:14px;text-transform:uppercase;letter-spacing:.3px}
.btn-red{background:var(--red);box-shadow:3px 4px 0 rgba(0,0,0,.12)}
.btn .knob{width:34px;height:34px;border-radius:50%;background:var(--white);display:flex;align-items:center;justify-content:center}
.btn .knob span{width:12px;height:12px;border-radius:50%;background:var(--navy)}
.nav .btn{padding:0 4px 0 16px;height:41px;width:161px;font-size:14px;margin-left:6px}
.hero-title{top:350px;left:62px;font-family:'Cinzel',serif;font-size:56px;font-weight:700;color:var(--white);letter-spacing:1px}
.hero-sub{top:425px;left:62px;width:380px;font-size:15.5px;line-height:24px;color:var(--white)}
.hero-btn{top:493px;left:61px;width:160px;height:40px;padding:0 4px 0 15px}
.about-frame{top:887px;left:163px;width:120px;height:299px;background:var(--red);border-radius:6px}
.photo{border:5px solid var(--white);box-shadow:0 2px 10px rgba(0,0,0,.2)}
.photo-a{top:866px;left:183px;width:300px;height:300px;background:radial-gradient(circle at 63% 40%,#d8c7a4 0%,#4a6b86 22%,#1a2a3c 55%,#0d1520 100%)}
.photo-b{top:1056px;left:335px;width:196px;height:196px;background:radial-gradient(circle at 40% 35%,#f4d48a 0%,#b9bbbd 30%,#e8e8e8 70%,#fafafa 100%)}
.about{top:888px;left:604px;width:440px}
h2.serif{font-family:'EB Garamond',serif;font-weight:600;color:var(--navy);font-size:32px;line-height:38px}
.about p,.cheaper p{font-size:12px;line-height:19.5px;color:var(--muted);margin-top:6px}
.about h2{margin-bottom:18px}
.about .btn{margin-top:18px;width:162px;height:40px;padding:0 4px 0 14px}
.cheaper{top:1386px;left:62px;width:300px}
.cheaper h2{margin-bottom:18px}
.card{top:1491px;width:225px;height:241px;background:var(--white);box-shadow:0 0 8px rgba(0,0,0,.12);text-align:center}
.card .badge{position:absolute;left:50%;top:-22px;margin-left:-43px;width:86px;height:86px;border-radius:50%;background:var(--white);border:2px solid var(--red);border-top-color:var(--white);display:flex;align-items:center;justify-content:center}
.card h3{margin-top:78px;font-size:15px;font-weight:500;color:#111}
.card .pill{display:block;margin:12px auto 0;width:135px;height:37px;border-radius:19px;color:var(--white);font-size:13.5px;line-height:37px}
.pill.red{background:var(--red)}
.pill.navy{background:var(--navy);margin-top:15px}
.price{font-size:18px;font-weight:600;color:var(--red);margin-top:5px}
.unit{font-size:12px;color:#555}
.card p{font-size:12px;line-height:19.5px;color:#555;margin:6px 20px 0}
.watermark{top:1382px;left:632px;font-family:'Cinzel',serif;font-weight:700;font-size:52px;color:rgba(255,255,255,.06);letter-spacing:2px}
.footer-col{top:1962px;color:var(--white)}
.footer-col h4{font-size:18px;font-weight:400;margin-bottom:10px}
.footer-col li{list-style:none;font-size:12px;line-height:22.5px;opacity:.92}
.footer-brand{top:1966px;left:60px;width:240px;color:var(--white)}
.footer-brand .brand{color:var(--white);font-size:27px}
.footer-brand .brand .dot{background:var(--white);width:26px;height:26px}
.footer-brand p{font-size:12px;line-height:19.5px;margin-top:12px;opacity:.92}
.contact-row{display:flex;align-items:center;gap:14px;font-size:11.5px;margin-bottom:20px}
.contact-row .box{width:34px;height:34px;background:var(--white);display:flex;align-items:center;justify-content:center}
.copyright{top:2232px;left:0;width:1200px;height:37px;background:var(--navy);color:var(--white);font-size:11.5px;text-align:center;line-height:37px}
</style>
</head>
<body>
<div class="page">

  <div class="abs topbar">
    <span>Welcome To VINDGERDI!</span>
    <div class="info">
      <div class="item"><span class="ico-circle"><svg width="13" height="13" viewBox="0 0 24 24"><path fill="#9b2d31" d="M6.6 10.8a15 15 0 0 0 6.6 6.6l2.2-2.2c.3-.3.7-.4 1-.2 1.1.4 2.3.6 3.6.6.6 0 1 .4 1 1V20c0 .6-.4 1-1 1A17 17 0 0 1 3 4c0-.6.4-1 1-1h3.5c.6 0 1 .4 1 1 0 1.3.2 2.5.6 3.6.1.3 0 .7-.2 1z"/></svg></span>Call: 555-0100</div>
      <div class="item"><span class="ico-circle"><svg width="14" height="12" viewBox="0 0 14 12"><rect x="1" y="2" width="12" height="8" rx="1" fill="none" stroke="#9b2d31" stroke-width="1.5"/><rect x="3" y="4" width="3" height="3" fill="#9b2d31"/><path d="M8 5h3M8 7h3" stroke="#9b2d31"/></svg></span>ID Number: 123456-7890</div>
    </div>
  </div>

  <header class="abs header">
    <div class="brand"><span class="dot"></span>VINDGERDI</div>
    <nav class="nav">
      <span class="active">Home</span>
      <span>Terms of Business</span>
      <span>Question &amp; Answer</span>
      <span>About Vindgerdi</span>
      <span class="btn btn-red">Contact Us<span class="knob"><span></span></span></span>
    </nav>
  </header>

  <svg class="abs" style="top:116px;left:0" width="1200" height="680" viewBox="0 0 1200 680" role="img" aria-label="Photo of a hydroelectric dam beside a river in a snowy mountain valley with power lines">
    <defs>
      <linearGradient id="heroGrad" x1="0" y1="0" x2="0" y2="1">
        <stop offset="0" stop-color="#4b5766"/>
        <stop offset=".35" stop-color="#7d8894"/>
        <stop offset=".6" stop-color="#3e4a55"/>
        <stop offset="1" stop-color="#1f3a42"/>
      </linearGradient>
    </defs>
    <path d="M0 0H1200V337C900 500 600 674 310 674C180 674 80 615 0 535Z" fill="url(#heroGrad)"/>
    <path d="M1200 337C900 500 600 674 310 674C180 674 80 615 0 535" fill="none" stroke="#9b2d31" stroke-width="3"/>
  </svg>
  <div class="abs hero-title">VINDGERDI</div>
  <p class="abs hero-sub">Vindgerdi reserves the right to change these terms of business.</p>
  <span class="abs btn btn-red hero-btn">Contact Us<span class="knob"><span></span></span></span>

  <div class="abs about-frame"></div>
  <div class="abs photo photo-a" role="img" aria-label="Illustration of a glowing light bulb with gears surrounded by technology icons"></div>
  <div class="abs photo photo-b" role="img" aria-label="Photo of a small figure plugging a glowing bulb into a wall socket"></div>

  <section class="abs about">
    <h2 class="serif">About Us</h2>
    <p>The customer can terminate the contract with Vindgerdi with three weeks' notice and the termination will then take effect at the end of next month. A longer notice period may be negotiated if the general user uses more than 0.5 GWh annually.</p>
    <p>Customers may terminate a contract with Vindgerdi if Vindgerdi significantly breaches its obligations.</p>
    <p>Vindgerdi may terminate the contract if the customer is not in arrears with payments. In the event of default by the customer, Vindgerdi will send a written demand for payment together with a warning that no payment will be made, which will result in termination of the contract.</p>
    <span class="btn btn-red">Learn More<span class="knob"><span></span></span></span>
  </section>

  <svg class="abs" style="top:1330px;left:0" width="1200" height="940" viewBox="0 0 1200 940">
    <path d="M549 0H1200V262H429V130C429 58 480 0 549 0Z" fill="#0d3468"/>
    <path d="M1200 408C1120 520 900 570 600 585C320 595 130 575 0 535V902H1200Z" fill="#9b2d31"/>
  </svg>
  <div class="abs watermark">VINDGERDI</div>

  <section class="abs cheaper">
    <h2 class="serif">Same electricity ~ just cheaper!</h2>
    <p>The customer can terminate the contract with Vindgerdi with three weeks' notice and the termination will then take effect at the end of next month. A longer notice period may be negotiated if the general user uses more than 0.5 GWh annually.</p>
  </section>

  <div class="abs card" style="left:420px">
    <div class="badge"><svg width="36" height="36" viewBox="0 0 24 24"><path fill="#9b2d31" d="M12 3 2 12h3v8h5v-5h4v5h5v-8h3z"/></svg></div>
    <h3>Welcome to business</h3>
    <span class="pill red">CAMPANY</span>
    <span class="pill navy">HOME</span>
  </div>
  <div class="abs card" style="left:667px">
    <div class="badge"><svg width="34" height="40" viewBox="0 0 20 24"><rect x="2" y="3" width="16" height="20" rx="2" fill="none" stroke="#9b2d31" stroke-width="1.6"/><rect x="6" y="1" width="8" height="4" rx="1" fill="#9b2d31"/><path d="M5 10h3M6.5 8.5v3M10 9h5M10 11h5M5 15h6M5 18h6" stroke="#9b2d31" stroke-width="1.3"/><text x="13" y="19" font-size="6" fill="#9b2d31" font-family="Poppins,sans-serif">$</text></svg></div>
    <h3>Price List</h3>
    <div class="price">6.95</div>
    <div class="unit">ISK / kWh</div>
    <div class="price" style="margin-top:12px">6.22</div>
    <div class="unit">ISK / kWh</div>
    <div class="unit" style="margin-top:4px">electric acceleration</div>
  </div>
  <div class="abs card" style="left:915px">
    <div class="badge"><svg width="30" height="40" viewBox="0 0 16 24"><path fill="#9b2d31" d="M10 0 1 14h6l-2 10 10-15H9z"/></svg></div>
    <h3>The future is exciting</h3>
    <p>exciting Let's make the electricity system smarter together. Vindgerdi uses artificial intelligence, data science and</p>
  </div>

  <div class="abs footer-brand">
    <div class="brand"><span class="dot"></span>VINDGERDI</div>
    <p>Our marketing strategy is to portray a tech company mindset and to show dedication to driving down the electricity price on the market.</p>
  </div>
  <div class="abs footer-col" style="left:337px">
    <h4>Site Map</h4>
    <ul><li>- Home</li><li style="margin-top:7px">- Terms of Business</li><li style="margin-top:7px">- Question &amp; Answer</li><li style="margin-top:7px">- About Vindgerdi</li></ul>
  </div>
  <div class="abs footer-col" style="left:612px">
    <h4>Contact Us</h4>
    <div class="contact-row"><span class="box"><svg width="16" height="20" viewBox="0 0 16 20"><path d="M8 1a6 6 0 0 0-6 6c0 5 6 11 6 11s6-6 6-11a6 6 0 0 0-6-6z" fill="none" stroke="#9b2d31" stroke-width="1.6"/><circle cx="8" cy="7" r="2" fill="#9b2d31"/></svg></span>Dæmigata 12, 101 Reykjavík</div>
    <div class="contact-row"><span class="box"><svg width="18" height="14" viewBox="0 0 18 14"><rect width="18" height="14" rx="1" fill="#9b2d31"/><path d="M1 1l8 6 8-6" fill="none" stroke="#fff" stroke-width="1.4"/></svg></span>info@vindgerdi.example</div>
    <div class="contact-row"><span class="box"><svg width="18" height="18" viewBox="0 0 24 24"><path fill="#9b2d31" d="M6.6 10.8a15 15 0 0 0 6.6 6.6l2.2-2.2c.3-.3.7-.4 1-.2 1.1.4 2.3.6 3.6.6.6 0 1 .4 1 1V20c0 .6-.4 1-1 1A17 17 0 0 1 3 4c0-.6.4-1 1-1h3.5c.6 0 1 .4 1 1 0 1.3.2 2.5.6 3.6.1.3 0 .7-.2 1z"/></svg></span>555-0100</div>
  </div>
  <div class="abs footer-col" style="left:888px">
    <h4>Terms of Business</h4>
    <ul><li>- Scope</li><li>- Gathering information and plan</li><li>- Dealer change</li><li>- User exchange</li><li>- Prices and payment terms</li><li>- End of contractual relationship</li><li>- Privacy</li><li>- Uncontrollable events</li></ul>
  </div>

  <div class="abs copyright">©2021 VINDGERDI - All Right Reserved.</div>
</div>
</body>
</html>
```